Bicycle dealer and service & repair center

The registered brand of our company, Rad Lindhof, means bicycle of the city Zurich (Switzerland) and is the largest dealer of e-bikes, folding bikes and cargo bikes in Switzerland. Rad Lindhof also sells a substantial amount of road bikes, mountainbikes, trailers and bicycles without electric motor. The more, we are known for special bikes (tandems, Swiss military bicycles, postman bicycles, and others).Rad Lindhof has around 10 highly skilled employees and runs a well-equipped service & repair center. We have around 50 brand dealerships for replacement parts, diagnostic devices and are proud about our after-sales service.Our website is fully functional (see www.rad-lindhof.ch) and available in three languages (DE, EN, FR for the french speaking part of Switzerland). Live stock information is provided by https://www.rad-lindhof.ch/en/rad.We need a redesign of our website. The focus should be on:- e-catalog with simple search and extended search - e-commerce (e.g. add to chart, favorites, text search, filter, sort, related products, similar products, most popular search, related articles, top listings, promotions...)- cross-selling with our affiliated company Rad Brunnegg, our bicycle shop in a city nearby Zurich.- service and repair- company (sustainable business, emission-free mobility, public relation, well-trained and friendly staff)- mobile friendlyness- maximize usability- maximize usage of display for useful information- easy to find relevant information- simple search functionalityKey audience is:- middle to high-price bicycle customers- existing and returning clients- prospective employees- members of the pressThe goal of the website and its redesign is:- increase the number of enquiries via website- increase online sales- share information with others (addtoany)- provide information about the right selection of bicycle (faq, detailed information about components) to reduce the admin associated with new enquiries- highlight special offers (e.g. free bicycle service slots, sunday exhibition)As Rad Lindhof has many returning customers and already high website traffic (according to SERP), the new design should be a smooth transition from the existing website.Websites we like:- https://tramofix.ch/- https://www.kurbelhaus.ch/- https://www.quandor.ch/- https://www.autoscout24.ch/deGood luck and have fun creating our new design!
Updates

website we also like: https://www.pedalora.ch/

Target Market(s)

Urban bicycle riders

Industry/Entity Type

Retail

Coding

Coded - Design and coding required

Number of Pages Required

5+ page

Font styles to use
Other font styles liked:
• Avenir (https://www.glyphbazar.com/fonts/typecraft/avenir/)

Colors

Designer to choose colors to be used in the design.

Requirements
Must have
• The actual content www.rad-lindhof.ch must be published with the new website design. Additional content should be added according to project description (see above).
Nice to have
• - we use the font type Avenir (https://www.glyphbazar.com/fonts/typecraft/avenir/) for business cards, leaflets etc
Should not have
• Frippery

```html
<!DOCTYPE html>
<html lang="en">
<head>
<meta charset="utf-8">
<title>Rad Lindhof – E-Bikes, Cargobikes, Service &amp; Repair</title>
<link href="https://fonts.googleapis.com/css2?family=Montserrat:wght@500;600;700;800&family=Roboto:wght@400;500;700&display=swap" rel="stylesheet">
<style>
:root{
  --blue:#2081b6;
  --blue-dark:#1a6f9e;
  --ink:#222;
  --text:#555;
  --muted:#999;
  --line:#e4e4e4;
  --grey-bg:#f1f2f4;
  --sale:#e43b3b;
  --star:#f3a712;
  --footer:#1e1e1e;
  --footer-bottom:#121212;
}
*{box-sizing:border-box;margin:0;padding:0}
html,body{width:1200px;height:4454px;overflow:hidden}
body{position:relative;font-family:Roboto,sans-serif;color:var(--text);background:#fff;font-size:14px}
.abs{position:absolute}
.h-font{font-family:Montserrat,sans-serif}
.btn{position:absolute;background:var(--blue);color:#fff;font-family:Montserrat,sans-serif;font-weight:600;font-size:15px;display:flex;align-items:center;justify-content:center;gap:7px;text-transform:uppercase}
.btn .dot{width:12px;height:12px;border-radius:50%;background:#fff;display:inline-block;position:relative}
.btn .dot::after{content:"";position:absolute;left:4px;top:3px;border-left:5px solid var(--blue);border-top:3px solid transparent;border-bottom:3px solid transparent}

.topbar{left:0;top:0;width:1200px;height:40px;background:var(--blue);color:#fff;font-size:15px}
.topbar .msg{position:absolute;left:110px;top:11px}
.topbar .social{position:absolute;right:112px;top:12px;display:flex;gap:12px;align-items:center;font-size:14px}
.topbar .social i{width:14px;height:14px;border-radius:50%;background:#fff;display:block;opacity:.9}

.header{left:0;top:40px;width:1200px;height:150px;background:#fff}
.logo{position:absolute;left:110px;top:48px;display:flex;align-items:center;gap:8px}
.logo .name{font-family:Montserrat,sans-serif;font-weight:800;font-size:33px;color:#111;letter-spacing:-.5px;line-height:1}
.logo .tag{font-size:9px;color:#555;margin-top:3px}
.logo .mark{width:62px;height:62px;border-radius:8px;background:var(--blue)}
.nav{position:absolute;left:505px;top:72px;display:flex;gap:27px;font-family:Montserrat,sans-serif;font-weight:600;font-size:15px;color:#222}
.nav-icons{position:absolute;left:1020px;top:70px;display:flex;gap:26px}

.hero{left:0;top:190px;width:1200px;height:559px;
  background:
    radial-gradient(ellipse 320px 420px at 90px 260px,rgba(92,62,30,.95),rgba(120,84,40,.6) 55%,transparent 80%),
    radial-gradient(ellipse 420px 160px at 560px 80px,rgba(250,236,200,.9),transparent 75%),
    radial-gradient(ellipse 500px 200px at 420px 470px,rgba(140,120,70,.7),transparent 75%),
    radial-gradient(ellipse 700px 260px at 950px 520px,rgba(60,90,30,.95),transparent 80%),
    linear-gradient(180deg,#6f8fa6 0%,#a9b6b8 22%,#d8c692 40%,#8d9a5a 58%,#5d7030 78%,#3b4a1e 100%)}
.hero-title{left:662px;top:312px;color:#fff;font-family:Montserrat,sans-serif;font-weight:700;font-size:48px;letter-spacing:.5px;text-shadow:0 1px 4px rgba(0,0,0,.3)}
.hero-sub{left:664px;top:378px;width:410px;color:#fff;font-size:18px;line-height:26px;text-shadow:0 1px 3px rgba(0,0,0,.35)}
.arrow-circle{position:absolute;width:40px;height:40px;border-radius:50%;background:rgba(0,0,0,.75);display:flex;align-items:center;justify-content:center}

.search-box{left:110px;top:622px;width:978px;height:266px;background:#fff;box-shadow:0 1px 6px rgba(0,0,0,.12)}
.search-title{position:absolute;left:0;top:48px;width:100%;text-align:center;font-family:Montserrat,sans-serif;font-weight:700;font-size:36px;color:#111}
.field{position:absolute;top:134px;width:221px}
.field label{display:block;font-family:Montserrat,sans-serif;font-weight:700;font-size:14px;color:#222;margin-bottom:12px}
.select{height:42px;border:1px solid var(--line);display:flex;align-items:center;justify-content:space-between;padding:0 8px 0 14px;font-size:12px;color:var(--muted)}
.select .caret{width:26px;height:26px;background:var(--blue);position:relative}
.select .caret::after{content:"";position:absolute;left:8px;top:11px;border-top:6px solid #fff;border-left:5px solid transparent;border-right:5px solid transparent}

.sec-title{font-family:Montserrat,sans-serif;font-weight:700;color:#111}
.card-title{position:absolute;left:42px;font-family:Montserrat,sans-serif;font-weight:700;font-size:25px;color:#111;display:flex;align-items:center;gap:16px}
.card-title .rule{height:1px;background:var(--line)}
.pager{position:absolute;display:flex;gap:4px}
.pager span{width:24px;height:24px;border:1px solid var(--line);display:flex;align-items:center;justify-content:center}

.product{position:absolute;top:1112px;width:220px;height:288px;border:1px solid var(--line);background:#fff;text-align:center}
.product .img{position:absolute;left:14px;top:30px;width:192px;height:150px}
.product .heart{position:absolute;right:10px;top:8px}
.product .pname{position:absolute;left:0;top:198px;width:100%;font-family:Montserrat,sans-serif;font-weight:500;font-size:16px;color:#333}
.product .stars{position:absolute;left:0;top:222px;width:100%;color:var(--star);font-size:10px;letter-spacing:1px}
.product .price{position:absolute;left:0;top:246px;width:100%;font-size:16px;font-weight:500}
.old{color:#666;text-decoration:line-through;margin-right:18px}
.new{color:var(--sale)}
.actions{display:flex;gap:10px}
.actions span{width:36px;height:36px;background:var(--blue);display:flex;align-items:center;justify-content:center}
.actions.small span{width:24px;height:24px}

/* product photo tones */
.tone-olive{background:radial-gradient(ellipse 46% 40% at 50% 55%,#7c9280 0%,#a9b8ab 45%,#eef1ee 75%,#fff 100%)}
.tone-black{background:radial-gradient(ellipse 46% 40% at 50% 55%,#3a3d40 0%,#8d9195 45%,#eceeef 75%,#fff 100%)}
.tone-lime{background:radial-gradient(ellipse 40% 46% at 50% 55%,#9cc43a 0%,#c8dc8e 40%,#eef3e2 72%,#fff 100%)}
.tone-trailer{background:radial-gradient(ellipse 44% 44% at 50% 52%,#3f4a56 0%,#8fae3e 30%,#cdd9b4 55%,#f2f4ee 78%,#fff 100%)}
.tone-brown{background:radial-gradient(ellipse 44% 36% at 50% 55%,#5a3e2a 0%,#a98a6e 42%,#efe8e1 74%,#fff 100%)}
.tone-red{background:radial-gradient(ellipse 44% 36% at 50% 55%,#c8313a 0%,#5a5d62 35%,#d9dbdd 62%,#fff 90%)}
.tone-steel{background:radial-gradient(ellipse 46% 40% at 50% 50%,#4a5058 0%,#8fa44c 32%,#c9ccd0 58%,#f4f5f6 80%,#fff 100%)}
.tone-white{background:radial-gradient(ellipse 46% 36% at 50% 48%,#2c2f33 0%,#b9bdc2 38%,#eff0f2 70%,#fff 100%)}
.tone-blue{background:radial-gradient(ellipse 46% 36% at 50% 48%,#2a4f7a 0%,#3d4148 35%,#c8cbd0 62%,#fff 90%)}

.grey{left:0;top:1639px;width:1200px;height:458px;background:var(--grey-bg)}
.grey2{left:0;top:2491px;width:1200px;height:1586px;background:var(--grey-bg)}
.card{position:absolute;background:#fff;box-shadow:0 1px 4px rgba(0,0,0,.08)}
.sim{position:absolute;top:99px;width:431px;height:218px;border:1px solid var(--line)}
.sim .img{position:absolute;left:0;top:0;width:216px;height:218px;border-right:1px solid var(--line)}
.sim .info{position:absolute;left:240px;top:18px}
.sim .info .pn{font-family:Montserrat,sans-serif;font-weight:500;font-size:17px;color:#222}
.sim .info .pr{font-size:13px;margin-top:8px}
.sim .info .pr .old{margin-right:6px;color:#888}
.sim .info .pr b{color:#333;font-weight:500}
.sim .stars{color:var(--star);font-size:13px;margin:7px 0 12px}
.countdown{position:absolute;left:216px;top:158px;width:214px;height:60px;border-top:1px solid var(--line);display:flex}
.countdown div{flex:1;text-align:center;font-size:12px;color:#333;padding-top:12px;line-height:20px;border-right:1px solid var(--line)}
.countdown div:last-child{border-right:0}
.countdown small{display:block;font-size:10px;color:#666}

.brochure{left:0;top:2097px;width:1200px;height:394px;
  background:
    radial-gradient(ellipse 260px 394px at 600px 394px,rgba(120,96,70,.85),transparent 80%),
    radial-gradient(ellipse 360px 220px at 180px 120px,rgba(196,120,30,.9),transparent 75%),
    radial-gradient(ellipse 380px 220px at 1020px 140px,rgba(214,132,40,.9),transparent 75%),
    radial-gradient(ellipse 300px 160px at 600px 70px,rgba(90,110,50,.9),transparent 75%),
    linear-gradient(180deg,#4d5a26 0%,#8a6a2a 30%,#b5762a 55%,#7a4a20 80%,#4a3018 100%)}
.brochure-title{left:0;top:2218px;width:1200px;text-align:center;color:#fff;font-family:Montserrat,sans-serif;font-weight:700;font-size:38px;text-shadow:0 2px 6px rgba(0,0,0,.35)}

.listing{position:absolute;top:95px;width:196px}
.listing .img{height:218px;border:1px solid var(--line);position:relative}
.listing .pn{text-align:center;margin-top:22px;font-family:Montserrat,sans-serif;font-weight:500;font-size:17px;color:#222}
.listing .pr{text-align:center;margin-top:6px;font-size:13px}
.listing .pr .old{margin-right:6px;color:#888}
.listing .pr b{color:#333;font-weight:500}

.footer{left:0;top:4077px;width:1200px;height:311px;background:var(--footer);color:#ddd}
.fcol{position:absolute;top:68px}
.fcol h4{font-family:Montserrat,sans-serif;font-weight:700;font-size:17px;color:#fff;text-decoration:underline;text-underline-offset:4px;margin-bottom:26px}
.fcol li{list-style:none;font-size:13.5px;height:26px;display:flex;align-items:center;gap:18px}
.fcol li::before{content:"»";color:#fff;font-size:13px}
.contact-row{display:flex;align-items:center;gap:22px;margin-bottom:14px;font-size:13.5px;line-height:22px}
.ci{width:36px;height:36px;border-radius:50%;background:#333;display:flex;align-items:center;justify-content:center;flex:none}
.follow li::before{display:none}
.follow li{height:41px;gap:18px}
.follow .ci{width:28px;height:28px}
.bottombar{left:0;top:4388px;width:1200px;height:66px;background:var(--footer-bottom);color:#ccc;font-size:14px}
.pay{position:absolute;top:24px;display:flex;gap:8px;left:888px}
.pay span{width:42px;height:22px;border-radius:3px;background:#fff}
</style>
</head>
<body>

<div class="abs topbar">
  <div class="msg">Free shipping On all orders over $100</div>
  <div class="social"><i></i><i></i><i></i><i></i><span>USD ▾</span></div>
</div>

<header class="abs header">
  <div class="logo">
    <div>
      <div class="name">RAD LINDHOF</div>
      <div class="tag">E-Bikes | Cargobikes | Velos | Service &amp; Reparaturen</div>
    </div>
    <div class="mark"></div>
  </div>
  <nav class="nav"><span>HOME</span><span>VELOS</span><span>NEWS</span><span>SERVICES</span><span>ABOUT US</span><span>FAQ</span></nav>
  <div class="nav-icons">
    <svg width="18" height="18" viewBox="0 0 18 18"><circle cx="7" cy="7" r="5.5" fill="none" stroke="#222" stroke-width="2.2"/><line x1="11" y1="11" x2="16" y2="16" stroke="#222" stroke-width="2.5"/></svg>
    <svg width="24" height="18" viewBox="0 0 24 18"><path d="M1 2h4l3 10h12l2-7H7" fill="none" stroke="#222" stroke-width="1.5"/><circle cx="9" cy="15.5" r="1.5" fill="#222"/><circle cx="18" cy="15.5" r="1.5" fill="#222"/></svg>
  </div>
</header>

<section class="abs hero" role="img" aria-label="Two mountain bikers riding a rocky trail at sunset above a valley"></section>
<div class="arrow-circle" style="left:32px;top:462px"><svg width="10" height="14"><path d="M8 1L2 7l6 6" stroke="#fff" stroke-width="2" fill="none"/></svg></div>
<div class="arrow-circle" style="left:1126px;top:462px"><svg width="10" height="14"><path d="M2 1l6 6-6 6" stroke="#fff" stroke-width="2" fill="none"/></svg></div>
<h1 class="abs hero-title">RAD LINDHOF</h1>
<p class="abs hero-sub">We offers the largest selection of pedelecs and s-pedelecs in Switzerland.</p>
<div class="btn" style="left:663px;top:453px;width:161px;height:43px">Read More <span class="dot"></span></div>

<section class="abs search-box">
  <h2 class="search-title">SEARCH TOUR PRODUCTS</h2>
  <div class="field" style="left:27px"><label>POWER:</label><div class="select">Select Power<span class="caret"></span></div></div>
  <div class="field" style="left:260px"><label>TYPE:</label><div class="select">Select Type<span class="caret"></span></div></div>
  <div class="field" style="left:495px"><label>BRAND:</label><div class="select">Select Brand<span class="caret"></span></div></div>
  <div class="field" style="left:729px"><label>PRICE:</label><div class="select">Select Price<span class="caret"></span></div></div>
  <div class="btn" style="left:386px;top:243px;width:206px;height:46px">Search Now <span class="dot"></span></div>
</section>

<h2 class="abs sec-title" style="left:110px;top:1008px;font-size:40px">RELATED PRODUCTS</h2>
<div class="abs select" style="left:866px;top:1012px;width:215px;height:38px;background:#fff">Filtered By<span class="caret" style="width:26px;height:26px"></span></div>

<div class="product" style="left:110px">
  <div class="img tone-olive" role="img" aria-label="Olive green trekking bicycle"></div>
  <svg class="heart" width="18" height="16" viewBox="0 0 18 16"><path d="M9 15S1 10 1 5a4 4 0 0 1 8-1 4 4 0 0 1 8 1c0 5-8 10-8 10z" fill="none" stroke="#2081b6" stroke-width="1.5"/></svg>
  <div class="pname">PRODUCT NAME</div><div class="stars">★★★★★</div>
  <div class="price"><span class="old">$94.00</span><span class="new">$72.00</span></div>
</div>
<div class="product" style="left:363px">
  <div class="img tone-black" role="img" aria-label="Black electric city bicycle"></div>
  <svg class="heart" width="18" height="16" viewBox="0 0 18 16"><path d="M9 15S1 10 1 5a4 4 0 0 1 8-1 4 4 0 0 1 8 1c0 5-8 10-8 10z" fill="none" stroke="#2081b6" stroke-width="1.5"/></svg>
  <div class="pname">PRODUCT NAME</div><div class="stars">★★★★★</div>
  <div class="price"><span class="old">$94.00</span><span class="new">$72.00</span></div>
</div>
<div class="product" style="left:616px;height:306px">
  <div class="img tone-lime" role="img" aria-label="Lime green folding bicycle"></div>
  <svg class="heart" width="18" height="16" viewBox="0 0 18 16"><path d="M9 15S1 10 1 5a4 4 0 0 1 8-1 4 4 0 0 1 8 1c0 5-8 10-8 10z" fill="#2081b6"/></svg>
  <div class="pname">PRODUCT NAME</div><div class="stars">★★★★★</div>
  <div class="price"><span class="old">$94.00</span><span class="new">$72.00</span></div>
</div>
<div class="actions abs" style="left:660px;top:1402px">
  <span><svg width="16" height="12"><ellipse cx="8" cy="6" rx="7" ry="5" fill="#fff"/><circle cx="8" cy="6" r="2.5" fill="#2081b6"/></svg></span>
  <span><svg width="16" height="14"><path d="M1 1h3l2 8h8l1-6H5" fill="none" stroke="#fff" stroke-width="1.6"/><circle cx="7" cy="12" r="1.4" fill="#fff"/><circle cx="13" cy="12" r="1.4" fill="#fff"/></svg></span>
  <span><svg width="16" height="14"><path d="M1 4h13M11 1l3 3-3 3M15 10H2M5 7l-3 3 3 3" fill="none" stroke="#fff" stroke-width="1.6"/></svg></span>
</div>
<div class="product" style="left:870px">
  <div class="img tone-trailer" role="img" aria-label="Green and grey child bike trailer"></div>
  <svg class="heart" width="18" height="16" viewBox="0 0 18 16"><path d="M9 15S1 10 1 5a4 4 0 0 1 8-1 4 4 0 0 1 8 1c0 5-8 10-8 10z" fill="none" stroke="#2081b6" stroke-width="1.5"/></svg>
  <div class="pname">PRODUCT NAME</div><div class="stars">★★★★★</div>
  <div class="price"><span class="old">$94.00</span><span class="new">$72.00</span></div>
</div>
<div class="btn" style="left:488px;top:1483px;width:224px;height:44px">View All Products <span class="dot"></span></div>

<div class="abs grey"></div>
<section class="card" style="left:110px;top:1689px;width:978px;height:360px">
  <div class="card-title" style="top:38px">SIMILAR PRODUCTS <span class="rule" style="width:560px"></span></div>
  <div class="pager" style="left:880px;top:42px"><span><svg width="6" height="10"><path d="M5 1L1 5l4 4" stroke="#999" fill="none"/></svg></span><span><svg width="6" height="10"><path d="M1 1l4 4-4 4" stroke="#999" fill="none"/></svg></span></div>

  <div class="sim" style="left:42px">
    <div class="img tone-brown" role="img" aria-label="Black and brown electric trekking bicycle"></div>
    <div class="info">
      <div class="pn">Product Name</div>
      <div class="pr"><span class="new">$50.00</span> <span class="old">$ 89.56</span><b>30%</b></div>
      <div class="stars">★★★★★</div>
      <div class="actions small">
        <span><svg width="12" height="11" viewBox="0 0 18 16"><path d="M9 15S1 10 1 5a4 4 0 0 1 8-1 4 4 0 0 1 8 1c0 5-8 10-8 10z" fill="#fff"/></svg></span>
        <span><svg width="12" height="11"><path d="M0 1h2l2 6h6l1-4H3" fill="none" stroke="#fff" stroke-width="1.5"/></svg></span>
        <span><svg width="12" height="9"><ellipse cx="6" cy="4.5" rx="5.5" ry="4" fill="#fff"/><circle cx="6" cy="4.5" r="2" fill="#2081b6"/></svg></span>
        <span><svg width="12" height="12"><path d="M2 6a4 4 0 0 1 7-3M10 6a4 4 0 0 1-7 3" stroke="#fff" stroke-width="1.6" fill="none"/></svg></span>
      </div>
    </div>
    <div class="countdown"><div>603<small>Days</small></div><div>10<small>Hours</small></div><div>19<small>Mins</small></div><div>03<small>Secs</small></div></div>
  </div>

  <div class="sim" style="left:507px">
    <div class="img tone-red" role="img" aria-label="Red and white electric city bicycle"></div>
    <div class="info">
      <div class="pn">Product Name</div>
      <div class="pr"><span class="new">$50.00</span> <span class="old">$ 89.56</span><b>30%</b></div>
      <div class="stars">★★★★★</div>
      <div class="actions small">
        <span><svg width="12" height="11" viewBox="0 0 18 16"><path d="M9 15S1 10 1 5a4 4 0 0 1 8-1 4 4 0 0 1 8 1c0 5-8 10-8 10z" fill="#fff"/></svg></span>
        <span><svg width="12" height="11"><path d="M0 1h2l2 6h6l1-4H3" fill="none" stroke="#fff" stroke-width="1.5"/></svg></span>
        <span><svg width="12" height="9"><ellipse cx="6" cy="4.5" rx="5.5" ry="4" fill="#fff"/><circle cx="6" cy="4.5" r="2" fill="#2081b6"/></svg></span>
        <span><svg width="12" height="12"><path d="M2 6a4 4 0 0 1 7-3M10 6a4 4 0 0 1-7 3" stroke="#fff" stroke-width="1.6" fill="none"/></svg></span>
      </div>
    </div>
    <div class="countdown"><div>603<small>Days</small></div><div>10<small>Hours</small></div><div>19<small>Mins</small></div><div>03<small>Secs</small></div></div>
  </div>
</section>

<section class="abs brochure" role="img" aria-label="Two cyclists riding a forest path in autumn leaves"></section>
<h2 class="abs brochure-title">DOWNLOAD OUR BROCHURE</h2>
<div class="btn" style="left:514px;top:2313px;width:172px;height:44px">Down Load <span class="dot"></span></div>

<div class="abs grey2"></div>

<section class="card" style="left:110px;top:2536px;width:978px;height:407px">
  <div class="card-title" style="top:38px">TOP LISTINGS <span class="rule" style="width:620px"></span></div>
  <div class="pager" style="left:880px;top:42px"><span><svg width="6" height="10"><path d="M5 1L1 5l4 4" stroke="#999" fill="none"/></svg></span><span><svg width="6" height="10"><path d="M1 1l4 4-4 4" stroke="#999" fill="none"/></svg></span></div>
  <div class="listing" style="left:42px"><div class="img tone-steel" role="img" aria-label="Folded child bike trailer"></div><div class="pn">Product Name</div><div class="pr"><span class="new">$50.00</span> <span class="old">$ 89.56</span><b>30%</b></div></div>
  <div class="listing" style="left:276px"><div class="img tone-white" role="img" aria-label="White and black city bicycle">
      <div class="actions small" style="position:absolute;left:36px;top:184px;gap:8px">
        <span><svg width="12" height="11" viewBox="0 0 18 16"><path d="M9 15S1 10 1 5a4 4 0 0 1 8-1 4 4 0 0 1 8 1c0 5-8 10-8 10z" fill="#fff"/></svg></span>
        <span><svg width="12" height="11"><path d="M0 1h2l2 6h6l1-4H3" fill="none" stroke="#fff" stroke-width="1.5"/></svg></span>
        <span><svg width="12" height="9"><ellipse cx="6" cy="4.5" rx="5.5" ry="4" fill="#fff"/><circle cx="6" cy="4.5" r="2" fill="#2081b6"/></svg></span>
        <span><svg width="12" height="12"><path d="M2 6a4 4 0 0 1 7-3M10 6a4 4 0 0 1-7 3" stroke="#fff" stroke-width="1.6" fill="none"/></svg></span>
      </div></div><div class="pn">Product Name</div><div class="pr"><span class="new">$50.00</span> <span class="old">$ 89.56</span><b>30%</b></div></div>
  <div class="listing" style="left:509px"><div class="img tone-blue" role="img" aria-label="Blue and black electric mountain bike"></div><div class="pn">Product Name</div><div class="pr"><span class="new">$50.00</span> <span class="old">$ 89.56</span><b>30%</b></div></div>
  <div class="listing" style="left:742px"><div class="img tone-trailer" role="img" aria-label="Green child bike trailer with tow bar"></div><div class="pn">Product Name</div><div class="pr"><span class="new">$50.00</span> <span class="old">$ 89.56</span><b>30%</b></div></div>
</section>

<section class="abs" style="left:110px;top:2986px;width:310px;height:140px;background:var(--blue);color:#fff;text-align:center">
  <div class="h-font" style="font-weight:700;font-size:34px;margin-top:12px;line-height:40px">SALE</div>
  <div style="width:200px;margin:0 auto;border-top:1px dashed rgba(255,255,255,.7);border-bottom:1px dashed rgba(255,255,255,.7);font-size:14px;font-family:Montserrat,sans-serif;font-weight:600;padding:2px 0">SAVE UPTO</div>
  <div class="h-font" style="font-weight:700;font-size:36px;line-height:46px">25% OFF</div>
</section>

<section class="card" style="left:110px;top:3161px;width:310px;height:254px;text-align:center">
  <div class="h-font" style="position:absolute;left:0;top:26px;width:100%;font-weight:700;font-size:20px;color:#111">NEWSLETTER</div>
  <div style="position:absolute;left:59px;top:38px;width:46px;height:1px;background:var(--line)"></div>
  <div style="position:absolute;left:205px;top:38px;width:46px;height:1px;background:var(--line)"></div>
  <svg style="position:absolute;left:128px;top:62px" width="54" height="48" viewBox="0 0 54 48"><rect x="2" y="18" width="50" height="28" fill="#fff" stroke="#e43b3b" stroke-width="2"/><path d="M2 18l25 16 25-16" fill="none" stroke="#e43b3b" stroke-width="2"/><circle cx="27" cy="14" r="12" fill="#e43b3b"/><circle cx="27" cy="14" r="4" fill="none" stroke="#fff" stroke-width="2"/></svg>
  <div style="position:absolute;left:0;top:128px;width:100%;font-size:13px;color:#888">Subscribe! New Items.</div>
  <div style="position:absolute;left:22px;top:160px;width:266px;height:36px;border:1px solid var(--line);font-size:11px;color:#999;line-height:34px">Enter your email</div>
  <div class="btn" style="left:104px;top:206px;width:103px;height:28px;font-size:11px">Sign Up <span class="dot" style="width:10px;height:10px"></span></div>
</section>

<section class="card" style="left:453px;top:2982px;width:635px;height:433px">
  <div class="card-title" style="left:32px;top:40px">TESTIMONIAL <span class="rule" style="width:320px"></span></div>
  <div class="pager" style="left:545px;top:44px"><span><svg width="6" height="10"><path d="M5 1L1 5l4 4" stroke="#999" fill="none"/></svg></span><span><svg width="6" height="10"><path d="M1 1l4 4-4 4" stroke="#999" fill="none"/></svg></span></div>
  <div style="position:absolute;left:232px;top:112px;width:90px;height:90px;border-radius:50%;background:var(--blue-dark);display:flex;align-items:center;justify-content:center;color:#fff;font-family:Georgia,serif;font-size:80px;line-height:1;padding-top:34px">“</div>
  <div role="img" aria-label="Portrait of a smiling customer" style="position:absolute;left:305px;top:112px;width:92px;height:92px;border-radius:50%;background:radial-gradient(circle at 55% 45%,#f1dcc8,#d9a97a 55%,#b98556);border:3px solid #fff;box-shadow:0 1px 4px rgba(0,0,0,.15)"></div>
  <p style="position:absolute;left:60px;top:244px;width:515px;text-align:center;font-size:12px;line-height:26px;color:#666">At vero eos et accusamus et iusto odio dignissimos ducimus blanditiis praesentium voluptatum deleniti atque corrupti quos dolores et quas molestias excepturi ocaecati cupiditate non provident, similique sunt in culpa qui officia deserunt mollitia animi laborum et dolorum fuga. Et harum quidem rerum expedita distinctio.</p>
  <div style="position:absolute;left:0;top:378px;width:100%;text-align:center;font-size:15px;color:#555;font-weight:500">Marten Keller, <span style="font-size:11px;color:#888;font-weight:400">Creative Manager.</span></div>
</section>

<section class="card" style="left:110px;top:3453px;width:978px;height:380px">
  <div class="card-title" style="top:40px">RELATED ARTICLES <span class="rule" style="width:560px"></span></div>
  <div class="pager" style="left:880px;top:44px"><span><svg width="6" height="10"><path d="M5 1L1 5l4 4" stroke="#999" fill="none"/></svg></span><span><svg width="6" height="10"><path d="M1 1l4 4-4 4" stroke="#999" fill="none"/></svg></span></div>
  <div role="img" aria-label="Mountain biker cornering on a dirt trail at dusk" style="position:absolute;left:42px;top:105px;width:277px;height:234px;background:radial-gradient(ellipse 120px 90px at 70% 25%,rgba(255,214,150,.9),transparent 75%),radial-gradient(ellipse 140px 80px at 50% 90%,rgba(60,40,24,.9),transparent 80%),linear-gradient(160deg,#c99a62,#7d5532 55%,#33241a)"></div>
  <div style="position:absolute;left:352px;top:105px;width:276px;height:234px;background:var(--blue);color:#fff;text-align:center">
    <div style="margin-top:40px;font-size:11px">20th April 2019</div>
    <div class="h-font" style="margin-top:22px;font-weight:700;font-size:14px">UNDOUBTABLE SOURCE</div>
    <div style="margin:14px auto 0;width:220px;font-size:13px;line-height:22px">At vero eos et accusamus et iusto odio dignissimos ducimus</div>
    <div style="margin-top:18px;font-size:13px;text-decoration:underline">Read More ➜</div>
  </div>
  <div role="img" aria-label="Cyclist riding a ridge against a red sunset" style="position:absolute;left:659px;top:105px;width:277px;height:234px;background:radial-gradient(ellipse 110px 60px at 30% 45%,rgba(255,190,120,.95),transparent 75%),linear-gradient(180deg,#7f6a7e 0%,#d0744a 38%,#9a4630 60%,#4a2e2a 80%,#2a1e1e 100%)"></div>
</section>

<section class="card" style="left:110px;top:3873px;width:978px;height:156px"></section>
<svg class="abs" style="left:66px;top:3942px" width="12" height="20"><path d="M10 2L2 10l8 8" stroke="#888" stroke-width="2" fill="none"/></svg>
<svg class="abs" style="left:1122px;top:3942px" width="12" height="20"><path d="M2 2l8 8-8 8" stroke="#888" stroke-width="2" fill="none"/></svg>
<div class="abs" style="left:144px;top:3906px;display:flex;gap:16px">
  <div style="width:171px;height:92px;border:1px solid var(--line);display:flex;align-items:center;justify-content:center;font-size:20px;color:#444">Kettwerk</div>
  <div style="width:171px;height:92px;border:1px solid var(--line);display:flex;align-items:center;justify-content:center;font-size:20px;color:#444">Nordlauf</div>
  <div style="width:171px;height:92px;border:1px solid var(--line);display:flex;align-items:center;justify-content:center;font-size:20px;color:#444">Felsgrat</div>
  <div style="width:171px;height:92px;border:1px solid var(--line);display:flex;align-items:center;justify-content:center;font-size:20px;color:#444">Talbruck</div>
  <div style="width:171px;height:92px;border:1px solid var(--line);display:flex;align-items:center;justify-content:center;font-size:20px;color:#444">Seewind</div>
</div>

<footer class="abs footer">
  <div class="fcol" style="left:110px"><h4>QUICK LINKS</h4><ul><li>Home</li><li>About Us</li><li>Services</li><li>Our Products</li><li>Contact Us</li><li>Shop Now</li></ul></div>
  <div class="fcol" style="left:342px"><h4>MY ACCOUNT</h4><ul><li>Order History</li><li>Wish List</li><li>Last Order</li><li>Help</li><li>Newsletter</li><li>Return Policy</li></ul></div>
  <div class="fcol" style="left:584px"><h4>CONTACT US</h4>
    <div class="contact-row"><span class="ci"><svg width="12" height="16"><path d="M6 15S1 9 1 6a5 5 0 0 1 10 0c0 3-5 9-5 9z" fill="none" stroke="#aaa" stroke-width="1.4"/><circle cx="6" cy="6" r="1.8" fill="#aaa"/></svg></span><span>Rad Lindhof GmbH, Lindenweg<br>14, CH-8050 Zurich</span></div>
    <div class="contact-row"><span class="ci"><svg width="14" height="14"><path d="M3 1l3 3-2 2c1 2 2 3 4 4l2-2 3 3-2 2C6 13 1 8 1 3z" fill="#aaa"/></svg></span><span>+41 (0) 44 000 12 34</span></div>
    <div class="contact-row"><span class="ci"><svg width="14" height="11"><rect x="1" y="1" width="12" height="9" fill="none" stroke="#aaa" stroke-width="1.3"/><path d="M1 1l6 5 6-5" fill="none" stroke="#aaa" stroke-width="1.3"/></svg></span><span>info@rad-lindhof.ch</span></div>
  </div>
  <div class="fcol follow" style="left:956px"><h4>FOLLOW US</h4><ul style="margin-top:-6px">
    <li><span class="ci"><i style="width:10px;height:10px;border-radius:50%;background:#fff;display:block"></i></span>Facepage</li>
    <li><span class="ci"><i style="width:10px;height:10px;border-radius:50%;background:#fff;display:block"></i></span>Chirper</li>
    <li><span class="ci"><i style="width:10px;height:10px;border-radius:50%;background:#fff;display:block"></i></span>Snapgram</li>
    <li><span class="ci"><i style="width:10px;height:10px;border-radius:50%;background:#fff;display:block"></i></span>Pinboard</li>
  </ul></div>
</footer>
<div class="abs bottombar">
  <div style="position:absolute;left:110px;top:24px">© Copyright 2019 Rad Lindhof. All Rights Reserved.</div>
  <div class="pay"><span></span><span></span><span></span><span></span></div>
  <div style="position:absolute;left:1148px;top:26px;font-size:12px">C10</div>
</div>

</body>
</html>
```